Massage-Creme label for a young pharmacy

We are a young pharmacy which is part of a big union. We developed for a customer a very good massage creme with aloe vera, coconut oil, and many more advantages and as well a massage jelly. All we need is a good and affordable label which is beatiful and helps us to promote our product. As we want to develop further products, it would be very cool to have a corporate label for all upcoming products.

Target Market(s)

professional masseurs and physiotherapists

Industry/Entity Type

Health And Wellness

Font styles to use
Sans Serif
Decorative

Colors

Designer to choose colors to be used in the design.

Requirements
Must have
• Professionally looking design (but I'm sure you are doing so... :-)
Nice to have
• Label can have any shape. What you see is just a bad label with corresponding sizes, so you can imagine how it would look like in the final state.
Should not have
• If possible, the label should not be completely black (although it might look cool) as we are printing it on our own Vestrel kp812-tx and black is difficult to print (and very costy).

```html
<!DOCTYPE html>
<html lang="de">
<head>
<meta charset="utf-8">
<title>Massage-Crème Etikett</title>
<link rel="stylesheet" href="https://fonts.googleapis.com/css2?family=Allura&family=Roboto:wght@400;500&family=Roboto+Condensed:wght@400&display=swap">
<style>
  :root {
    --bg: #dfeeee;
    --white: #ffffff;
    --green-light: #9cc94e;
    --green: #6bb13e;
    --green-deep: #4f9c37;
    --green-edge: #2d8548;
    --ink: #1c1c1c;
    --red: #e0201c;
  }
  * { margin: 0; padding: 0; box-sizing: border-box; }
  html, body { width: 1200px; height: 900px; overflow: hidden; background: var(--bg); }
  .canvas { position: relative; width: 1200px; height: 900px; }

  .label {
    position: absolute; left: 112px; top: 45px;
    width: 976px; height: 810px; display: flex;
    box-shadow: 0 6px 24px rgba(0,0,0,.12);
  }
  .panel { position: relative; height: 100%; background: var(--white); overflow: hidden; }
  .panel--front { width: 510px; }
  .panel--back { width: 466px; }
  .panel__shape { position: absolute; inset: 0; width: 100%; height: 100%; }

  .title {
    position: absolute; font-family: "Allura", cursive; font-weight: 400; color: var(--ink);
    font-size: 64px; line-height: 1; white-space: nowrap;
  }
  .subtitle {
    position: absolute; display: flex; align-items: center; gap: 14px;
    font-family: "Roboto", sans-serif; font-size: 12px; color: var(--ink); letter-spacing: .2px;
  }
  .subtitle::before, .subtitle::after { content: ""; height: 2px; background: var(--ink); width: 60px; }

  .panel--front .title { left: 112px; top: 100px; transform: rotate(-4deg); }
  .panel--front .subtitle { left: 116px; top: 180px; }
  .panel--back .title { left: 80px; top: 34px; transform: rotate(-3deg); }
  .panel--back .subtitle { left: 80px; top: 122px; }

  .badge { position: absolute; left: 78px; top: 266px; width: 136px; height: 80px; }
  .badge__text {
    position: absolute; inset: 0; display: flex; align-items: center; justify-content: center;
    text-align: center; font-family: "Roboto", sans-serif; font-size: 14px; line-height: 1.1; color: var(--ink);
  }

  .visual {
    position: absolute; left: 90px; top: 480px; width: 360px; height: 250px;
    border-radius: 50%;
    background: radial-gradient(ellipse closest-side at 50% 50%, #8cc46a 0%, #9fbf76 40%, rgba(205,175,125,.7) 72%, rgba(230,220,190,0) 100%);
  }

  .info {
    position: absolute; left: 46px; right: 46px; top: 282px;
    font-family: "Roboto", sans-serif; color: var(--white); text-align: center;
    font-size: 12.5px; line-height: 1.3;
  }
  .info p { margin-bottom: 16px; }
  .info__ph { display: inline-block; padding: 0 6px 4px; border-bottom: 1.5px solid var(--white); position: relative; }
  .info__ph::after { content: ""; position: absolute; left: 50%; bottom: -4px; width: 5px; height: 5px; margin-left: -2px; border-radius: 50%; background: var(--green-edge); border: 1px solid var(--white); }
  .info__note { font-size: 10.5px; margin-top: 14px; }
  .info__box {
    margin: 0 38px; border: 2px solid var(--white); padding: 6px 10px;
    font-size: 10px; line-height: 1.3;
  }

  .brand {
    position: absolute; left: 216px; top: 644px; display: flex; align-items: center; gap: 6px;
    font-family: "Roboto", sans-serif; font-weight: 500; font-size: 12px; color: var(--white);
  }
  .brand__mark { width: 10px; height: 10px; background: var(--white); }
  .brand__sub { display: block; font-weight: 500; font-size: 9px; }

  .meta {
    position: absolute; left: 70px; top: 684px; font-family: "Roboto Condensed", sans-serif;
    font-size: 9px; line-height: 1.35; color: var(--white);
  }
  .ingredients {
    position: absolute; left: 70px; right: 70px; top: 716px;
    font-family: "Roboto Condensed", sans-serif; font-size: 8.5px; line-height: 1.3; color: var(--white);
  }
  .volume {
    position: absolute; left: 0; right: 0; top: 768px; text-align: center;
    font-family: "Roboto Condensed", sans-serif; font-size: 16px; color: var(--white);
  }
</style>
</head>
<body>
<div class="canvas">
  <div class="label">

    <section class="panel panel--front">
      <svg class="panel__shape" viewBox="0 0 510 810" preserveAspectRatio="none" aria-hidden="true">
        <defs>
          <linearGradient id="frontGreen" x1="0" y1="0" x2="0" y2="1">
            <stop offset="0" stop-color="#b7d84e"/>
            <stop offset=".45" stop-color="#7dbb41"/>
            <stop offset="1" stop-color="#4f9c37"/>
          </linearGradient>
        </defs>
        <path d="M392,0 C470,120 470,300 380,430 C300,540 170,600 120,810 L510,810 L510,0 Z" fill="var(--green-edge)"/>
        <path d="M412,0 C490,120 488,300 402,432 C322,548 196,610 150,810 L510,810 L510,0 Z" fill="url(#frontGreen)"/>
      </svg>
      <h1 class="title">Massage-Crème</h1>
      <div class="subtitle">COCONUT - ALOE VERA</div>
      <div class="badge">
        <svg viewBox="0 0 136 80" width="136" height="80" aria-hidden="true">
          <polygon fill="#fff" stroke="var(--red)" stroke-width="3"
            points="68,4 78,14 92,6 96,18 112,14 110,26 128,28 118,38 132,46 116,52 122,66 106,64 102,76 88,68 76,78 68,68 58,78 46,68 32,76 28,64 12,66 18,52 4,46 16,38 8,28 24,26 22,14 38,18 42,6 56,14"/>
        </svg>
        <div class="badge__text">energetisch<br>leitend !</div>
      </div>
      <div class="visual" role="img" aria-label="Illustration: Aloe-Vera-Blätter, aufgebrochene Kokosnuss und Ölfläschchen"></div>
    </section>

    <section class="panel panel--back">
      <svg class="panel__shape" viewBox="0 0 466 810" preserveAspectRatio="none" aria-hidden="true">
        <defs>
          <linearGradient id="backGreen" x1="0" y1="0" x2="0" y2="1">
            <stop offset="0" stop-color="#8ec447"/>
            <stop offset="1" stop-color="#5aa83a"/>
          </linearGradient>
        </defs>
        <path d="M0,262 C30,190 130,178 250,168 C360,158 430,134 466,98 L466,810 L0,810 Z" fill="var(--green-edge)"/>
        <path d="M0,284 C34,212 136,200 256,190 C364,180 434,158 466,122 L466,810 L0,810 Z" fill="url(#backGreen)"/>
      </svg>
      <h2 class="title">Massage-Crème</h2>
      <div class="subtitle">COCONUT - ALOE VERA</div>

      <div class="info">
        <p>Hochwertige und sehr hautschonende Emulsion mit hervorragendem Gleitverhalten für die professionelle Massage.</p>
        <p>Hilft durch den hohen Gehalt an Aloe Vera-Gel (50%), die Feuchtigkeit der Haut zu erhalten und schützt durch die Zugabe von Panthenol (= Provitamin B5) und Allantoin vor Hautreizungen.</p>
        <p>Speziell für die (bio-)energetische Massage entwickelt.</p>
        <span class="info__ph">pH-neutral für die Haut (pH-Wert = 5.5)</span>
        <p class="info__note">Bei der Entwicklung unserer Produkte legen wir grössten Wert auf gute Verträglichkeit und hochwertige Rohstoffe.</p>
        <div class="info__box">Dieses Produkt ist frei von Parabenen, Mineralölen (Paraffin/Vaseline), Silikonen, Farbstoffen und Mikroplastik (Acrylate).</div>
      </div>

      <div class="brand">
        <span class="brand__mark"></span>
        <span>Lindenhof<span class="brand__sub">Apotheke Dr. Maurer</span></span>
      </div>

      <div class="meta">Exp: 03/2021<br>Lot: 913015/A</div>
      <p class="ingredients">Zus.: water (aqua), cetearyl isononanoate, ethylhexyl stearate, cocos nucifera (coconut) oil, acrylates copolymer, glycerin, glyceryl stearate citrate, cetearyl alcohol, phenoxyethanol, caprylyl glycol, panthenol, sodium citrate, xanthan gum, disodium phosphate, citric acid, aloe barbadensis leaf juice extract, allantoin, parfum</p>
      <div class="volume">℮ 1000 ml</div>
    </section>

  </div>
</div>
</body>
</html>
```